Re-Design of a 1 Pager IT Security Website

Please create a 1 Pager design for this website and all its elements: http://www.quillstonebrightmarsh.com/

Colours, Fonts etc: You can select whatever you prefer

```html
<!DOCTYPE html>
<html lang="en">
<head>
<meta charset="utf-8">
<title>Veltrana — Protect yourself from Ransomware</title>
<link href="https://fonts.googleapis.com/css2?family=Poppins:wght@400;500;600;700&display=swap" rel="stylesheet">
<style>
:root{
  --navy:#0a2b4a;
  --navy-deep:#061d34;
  --yellow:#f8c12c;
  --ink:#1f2a37;
  --muted:#3d4754;
  --white:#ffffff;
  --paper:#eef1f4;
  --page:#fbfcfd;
}
*{margin:0;padding:0;box-sizing:border-box}
html,body{width:1152px;height:1200px;overflow:hidden;background:var(--paper);font-family:'Poppins',sans-serif;color:var(--ink)}
.stage{position:absolute;left:0;top:0;width:1882px;height:1960px;transform:scale(0.61211);transform-origin:0 0}
.page{position:absolute;width:592px;height:1809px;background:var(--page);overflow:hidden;box-shadow:0 10px 40px rgba(6,29,52,.18)}
.page--left{left:259px;top:59px}
.page--right{left:1045px;top:69px}
.abs{position:absolute}
.media{position:absolute}
.center{left:0;right:0;text-align:center}
.accent{color:var(--yellow)}
/* hero */
.hero{left:0;top:0;width:592px;height:293px;background:radial-gradient(ellipse at 60% 40%,#2d5f8a 0%,#123a60 35%,#071e38 75%,#040f20 100%)}
.nav-logo{left:63px;top:16px;color:#fff;font-weight:600;font-size:15px}
.nav-link{top:20px;color:#fff;font-size:8.5px}
.nav-link--active{border-bottom:1px solid #fff;padding-bottom:2px}
.btn-touch{left:432px;top:12px;width:95px;height:27px;border-radius:14px;background:var(--yellow);color:var(--navy);font-size:8.5px;font-weight:500;display:flex;align-items:center;justify-content:center}
.hero-kicker{top:80px;color:#fff;font-size:21px}
.hero-title{top:112px;color:#fff;font-size:36px;font-weight:700;letter-spacing:.5px}
.hero-rule{left:231px;top:162px;width:130px;height:1px;background:#fff}
.hero-sub{top:180px;color:#fff;font-size:9.5px}
.btn-outline{left:210px;top:212px;width:171px;height:35px;border:1px solid #fff;border-radius:18px;color:#fff;font-size:12px;display:flex;align-items:center;justify-content:center}
/* about */
.about-blob-back{left:42px;top:350px;width:240px;height:232px;border-radius:52% 48% 46% 54%/58% 44% 56% 42%;background:#9ea3a8}
.about-photo{left:44px;top:372px;width:232px;height:205px;border-radius:46% 54% 50% 50%/52% 48% 52% 48%;background:linear-gradient(135deg,#8a6a4c,#3f3a3e 55%,#a44a3a)}
.h-section{font-size:15px;font-weight:600;color:var(--navy)}
.body{font-size:8px;line-height:14.5px;color:var(--ink)}
.small{font-size:7px;line-height:13.3px;color:var(--ink)}
.tiny{font-size:6.4px;line-height:10.5px;color:var(--ink);text-align:center}
.photo-band{left:0;top:745px;width:592px;height:175px;background:linear-gradient(90deg,#1b1b1e 0%,#3a3a3d 45%,#b9bbbd 70%,#dcdcdc 100%)}
.play{left:281px;top:815px;width:37px;height:37px}
/* types */
.types-band{left:0;top:1190px;width:592px;height:175px;background:var(--navy)}
.types-card{left:68px;top:1110px;width:455px;height:205px;background:#fff;border-radius:8px}
.type-col{top:1140px;width:100px}
.type-title{font-size:8.5px;line-height:12px;font-weight:500;color:var(--navy);text-align:center}
.type-body{margin-top:12px}
.divider{top:1180px;width:1px;height:105px;background:#c9ced4}
.link-more{font-size:9px;font-weight:500;display:flex;align-items:center;gap:10px}
.article{left:76px;top:1480px;width:440px;text-align:center;display:flex;flex-direction:column;align-items:center}
.article p{font-size:6.9px;line-height:13.2px}
.article p + p{margin-top:13px}
.article .link-more{margin-top:8px}
/* right page */
.shot{border-radius:8px}
.bracket{border:1.5px solid var(--yellow);border-radius:6px}
.q-title{font-size:12.5px;line-height:18px;font-weight:600;color:var(--navy)}
.q-body{font-size:7px;line-height:13.3px;color:var(--ink)}
.form-photo{left:0;top:1236px;width:592px;height:446px;background:linear-gradient(160deg,#5a5660 0%,#8e8482 35%,#b7a89a 60%,#8c6a50 100%)}
.form-card{left:238px;top:1298px;width:289px;height:320px;background:#fff;border-radius:10px}
.form-title{left:30px;top:22px;font-size:11.5px;color:var(--ink)}
.form-label{left:30px;font-size:8.5px;color:var(--ink)}
.form-field{left:30px;width:228px;background:#f5f7f9;border-radius:3px}
.btn-submit{left:163px;top:265px;width:95px;height:36px;border-radius:18px;background:var(--yellow);color:var(--navy);font-size:9px;font-weight:500;display:flex;align-items:center;justify-content:center}
.footer{left:0;top:1682px;width:592px;height:127px;background:var(--navy)}
.footer-title{top:32px;color:#fff;font-size:10px;word-spacing:3px}
.footer-links{top:68px;left:152px;display:flex;gap:36px;color:#fff;font-size:6.5px;font-weight:500}
.footer-copy{top:99px;color:#fff;font-size:5.5px}
</style>
</head>
<body>
<div class="stage">

  <!-- LEFT PAGE -->
  <section class="page page--left">
    <div class="media hero" role="img" aria-label="Dark blue photo of a glowing padlock on a circuit board"></div>
    <div class="abs nav-logo">Logo</div>
    <div class="abs nav-link nav-link--active" style="left:190px">Home</div>
    <div class="abs nav-link" style="left:246px">About</div>
    <div class="abs nav-link" style="left:301px">Contact</div>
    <div class="abs nav-link" style="left:366px">FAQ's</div>
    <div class="abs btn-touch">Get In Touch</div>
    <div class="abs center hero-kicker">Learn how to protect yourself from</div>
    <div class="abs center hero-title">Ransomware</div>
    <div class="abs hero-rule"></div>
    <div class="abs center hero-sub">Keep your computer safe and understand how to act in case of an successful attack</div>
    <div class="abs btn-outline">Learn More</div>

    <div class="abs about-blob-back"></div>
    <div class="media about-photo" role="img" aria-label="Photo of two colleagues working together at a laptop"></div>
    <div class="abs h-section" style="left:327px;top:386px"><span class="accent">About</span> us</div>
    <p class="abs body" style="left:327px;top:424px;width:205px">Veltrana (company registration number CHE-418.902.617) was started in 2018 as a public limited company in Lindmoor, Norvania. Our analysts have long-standing relationships with various players on the Darknet. These personal relationships make it possible for Veltrana to repeatedly obtain the latest data leaks. Those unique data leaks are published by the press around the world.</p>

    <div class="abs center h-section" style="top:655px"><span class="accent">Ransomware</span> in a Nutshell</div>
    <p class="abs small" style="left:81px;top:684px;width:430px;text-align:center;font-size:7.5px">Ransomware is a very dangerous cyber threat to all organisations and individuals. Ransomware is a type of malicious software that may block access to files or devices until the victim pays a ransom.The ransom is usually demanded in cryptocurrency.</p>

    <div class="media photo-band" role="img" aria-label="Video still of a stressed person holding their head in front of a laptop"></div>
    <svg class="abs play" viewBox="0 0 37 37"><circle cx="18.5" cy="18.5" r="18.5" fill="#f8c12c"/><path d="M13 15h11l-5.5 8z" fill="#0a2b4a"/></svg>

    <div class="abs center" style="top:998px;font-size:10px;color:var(--navy)">What are</div>
    <div class="abs center h-section" style="top:1015px">Common <span class="accent">ransomware</span> types?</div>
    <div class="abs center" style="top:1042px;font-size:8px">here are many different types of ransomware. Here are four typical categories:</div>

    <div class="abs types-band"></div>
    <div class="abs types-card"></div>
    <svg class="abs" style="left:60px;top:1085px" width="472" height="110" viewBox="0 0 472 110">
      <path d="M5 100V32a10 10 0 0 1 10-10h442a10 10 0 0 1 10 10v68" fill="none" stroke="#0a2b4a" stroke-width="3"/>
      <circle cx="60" cy="22" r="21" fill="#f8c12c"/>
      <circle cx="177" cy="22" r="21" fill="#0a2b4a"/>
      <circle cx="294" cy="22" r="21" fill="#0a2b4a"/>
      <circle cx="412" cy="22" r="21" fill="#0a2b4a"/>
      <g font-family="Poppins,sans-serif" font-weight="600" font-size="15" text-anchor="middle">
        <text x="60" y="28" fill="#0a2b4a">01</text>
        <text x="177" y="28" fill="#f8c12c">02</text>
        <text x="294" y="28" fill="#f8c12c">03</text>
        <text x="412" y="28" fill="#f8c12c">04</text>
      </g>
    </svg>
    <div class="abs type-col" style="left:70px">
      <div class="type-title">Ransomware that fakes something</div>
      <p class="tiny type-body">Scareware fakes a problem on the computer. For example, it could be a warning that a virus or malware has been found on the PC. The software then redirects the user to a website where the problem can be solved for a fee.</p>
    </div>
    <div class="abs divider" style="left:179px"></div>
    <div class="abs type-col" style="left:186px">
      <div class="type-title">Ransomware that Encrypts something</div>
      <p class="tiny type-body">Encryptors are the most common type of ransomware that encrypts all data and requires a key to unlock it, which can usually be purchased within a short period of time.</p>
    </div>
    <div class="abs divider" style="left:296px"></div>
    <div class="abs type-col" style="left:304px">
      <div class="type-title">Ransomware that leaks data</div>
      <p class="tiny type-body">This type of ransomware is called Doxware. Doxware often tries to force the user or the company to pay by threatening to publish confidential information online at a "Hall of Shame".</p>
    </div>
    <div class="abs divider" style="left:413px"></div>
    <div class="abs type-col" style="left:418px">
      <div class="type-title">Ransomware that locks something</div>
      <p class="tiny type-body">Instead of preventing access to files or applications, this ransomware type prevent the end user's device from being used. For example, key combinations (CTRL+ALT+DEL) are also locked, so that the user can no longer access his current work.</p>
    </div>
    <div class="abs link-more accent" style="left:356px;top:1334px">Learn About More Types
      <svg width="40" height="6" viewBox="0 0 40 6"><path d="M0 3h38M35 0.5l3 2.5-3 2.5" stroke="#f8c12c" fill="none" stroke-width="1"/></svg></div>

    <div class="abs center h-section" style="top:1440px">What if you don't pay the <span class="accent">ransom?</span></div>
    <div class="abs article">
      <p>If one does not pay the ransom and has no backup, the data is usually lost forever. Sometimes, however, the data ends up on the dark web and the affected companies are exposed. Thus, it is not the loss of the data that is the angle with which the hackers build up pressure, but the reputation damage caused by the lost data. This damage can be much greater than the value of the individual data. For example, who wants to do business with a bank that can't even protect itself? Every potential customer will not weigh his own money in security and go to a competitor.</p>
      <p>In the darknet, some hacker collectives operate websites where the attacked companies are exposed at a "hall of shame". This is where the complete data sets are published for everyone to see. By using free download links, all data can then also be downloaded immediately. Often, these data sets contain personal information about employees. Such a violation of privacy due to insufficient protection can lead to high penalties due to legal requirements such as GDPR. But unfortunately, the data leaks also often affect customers and partners of the involved organization, depending on the position of the employee who was hacked.</p>
      <p>The hackers are of course aware of the explosive nature of such revelations and have no scruples about making their threats come true. The Veltrana research team (https://www.veltrana.io) has recently noticed an accumulation of such activity on the dark web. A recent example was the Grimvale ransomware group. After ceasing all operations for several months between November 21 and February 22, the Grimvale ransomware is now active again. The increase in activity was noticed after the ransomware group added 21 new victims to its data leak site in a single month in April. Grimvale has become very active compared to the past. Comparison with other ransomware groups in April: Ashlock published 103 victims and Hollowmere – 45 victims, Grimvale's victims have increased massively, from 1 to 21. The industrial sector was Grimvale's main target: 45% of its attacks affected industrial companies and 27% targeted technology companies. Companies that know which sectors the ransomware group attacks most often should consider the possibility of being the next target of this gang and prepare accordingly.</p>
      <div class="link-more" style="color:var(--navy)">Read More
        <svg width="40" height="6" viewBox="0 0 40 6"><path d="M0 3h38M35 0.5l3 2.5-3 2.5" stroke="#0a2b4a" fill="none" stroke-width="1"/></svg></div>
    </div>
  </section>

  <!-- RIGHT PAGE -->
  <section class="page page--right">
    <div class="abs" style="left:76px;top:-6px;width:440px;text-align:center">
      <p class="small">their threats come true. The research team has recently noticed an accumulation of such activity on the dark web. A recent example was the Grimvale ransomware group. After ceasing all operations for several months between November 21 and February 22, the Grimvale ransomware is now active again. The increase in activity was noticed after the ransomware group added 21 new victims to its data leak site in a single month in April. Grimvale has become very active compared to the past. Comparison with other ransomware groups in April: Ashlock published 103 victims and Hollowmere – 45 victims, Grimvale's victims have increased massively, from 1 to 21. The industrial sector was Grimvale's main target: 45% of its attacks affected industrial companies and 27% targeted technology companies. Companies that know which sectors the ransomware group attacks most often should consider the possibility of being the next target of this gang and prepare accordingly.</p>
    </div>
    <div class="abs link-more" style="left:243px;top:125px;color:var(--navy)">Read More
      <svg width="40" height="6" viewBox="0 0 40 6"><path d="M0 3h38M35 0.5l3 2.5-3 2.5" stroke="#0a2b4a" fill="none" stroke-width="1"/></svg></div>

    <div class="abs bracket" style="left:37px;top:420px;width:87px;height:71px"></div>
    <div class="media shot" style="left:63px;top:212px;width:254px;height:265px;background:linear-gradient(135deg,#1d3f6a 0%,#b8402e 45%,#4a1e24 75%,#11243c 100%)" role="img" aria-label="Photo of a worried man looking at a laptop showing a ransomware warning"></div>
    <div class="abs q-title" style="left:338px;top:213px;width:165px">How can you get infected by ransomware?</div>
    <p class="abs q-body" style="left:338px;top:263px;width:192px">Infection by ransomware usually occurs through interaction with a user. For example, an attacker might send an email with an attachment containing the malware or download it from the Internet downstream. Usually, such malware is distributed as part of phishing attacks. But there are many other ways how the malware can get onto the PC. The hacker can also hide the malware in downloads on websites. For this purpose, the criminal can create websites himself, which are very similar to a regular reputable websites. Using freely available tools, complete websites can be easily even cloned and thanks to typosquatting technique, the corresponding domains can be purchased as well. However, the possibilities to bring malware onto a PC are even more diverse.</p>

    <div class="abs bracket" style="left:472px;top:534px;width:87px;height:303px"></div>
    <div class="media shot" style="left:273px;top:553px;width:254px;height:265px;background:linear-gradient(160deg,#1b3a5c 0%,#5d86a8 45%,#2a4e70 70%,#0f253e 100%)" role="img" aria-label="Photo of a person at a keyboard with glowing medical data overlays"></div>
    <div class="abs q-title" style="left:63px;top:631px;width:190px">How do you know if your data might be already exposed in the darknet?</div>
    <p class="abs q-body" style="left:63px;top:701px;width:185px">Veltrana offers a service that will find leaked data or your organisation mentioned on "ransomware hall of shame websites".</p>

    <div class="abs bracket" style="left:41px;top:878px;width:87px;height:71px"></div>
    <div class="media shot" style="left:64px;top:894px;width:254px;height:265px;background:linear-gradient(135deg,#0e2748 0%,#2d5a8e 45%,#6e92c4 60%,#122c50 100%)" role="img" aria-label="Photo of a hand typing on a keyboard with glowing security icons"></div>
    <div class="abs q-title" style="left:338px;top:895px;width:165px">How can you avoid a Ransomware attack?</div>
    <p class="abs q-body" style="left:338px;top:946px;width:192px">Thebest defense is the right behavior. Be suspicious of all downloads, attachments, etc. and only run software if you trust the creator. This includes macros in office applications. Also, keep your operating system and all applications patched and up to date to ensure that you have fewer vulnerabilities that a hacker can exploit. Also, make sure that you are a regular user with minimal privileges and are not also an administrator. Install antivirus software that detects malicious programs like ransomware and enable all security features offered by the operating system (e.g. built-in system protection). And of course, back up your files regularly and automatically! This won't prevent a ransomware attack, but it can significantly reduce the damage caused by such an attack.</p>

    <div class="media form-photo" role="img" aria-label="Photo of hands using a laptop with a USB security key"></div>
    <div class="abs form-card">
      <div class="abs form-title">WANT TO KNOW MORE?</div>
      <div class="abs form-label" style="top:50px">Your Email</div>
      <div class="abs form-field" style="top:68px;height:40px"></div>
      <div class="abs form-label" style="top:126px">Message</div>
      <div class="abs form-field" style="top:144px;height:100px"></div>
      <div class="abs btn-submit">Submit</div>
    </div>

    <footer class="abs footer">
      <div class="abs center footer-title">Protect from ransomware</div>
      <nav class="abs footer-links"><span>ABOUT</span><span>WORKS</span><span>GUIDELINES</span><span>MORE</span><span>CONTACT</span></nav>
      <div class="abs center footer-copy">ALL RIGHT RESERVED © Veltrana.io 2022</div>
    </footer>
  </section>

</div>
</body>
</html>
```